Networking Events Calendar/Diary

We need a responsive website that can act as both an online diary/calendar and a resource for community and networking events similar to brimtolvenquarrix.com (we do not want a clone, but one with similar functionality). We need to be able to host adverts, have a client area for clients to add their own events to the diary. This needs to have the functionality that clients have to pay to add recurring events. Some integration would be useful so that if a clients already has their own online diary on their website then using an API possibly to also add that event into our online diary

Industry/Entity Type

Events

Coding

Coded - Design and coding required

Number of Pages Required

5+ page

Requirements
Must have
• My project must have a calendar area, space for ads, be responsive and easily viewable on mobile. A subscribers area for clients and a way to purchase premium status so that premium events are highlighted.

```html
<!DOCTYPE html>
<html lang="en">
<head>
<meta charset="utf-8">
<title>Kelvara Events – Networking Events Directory</title>
<link rel="stylesheet" href="https://fonts.googleapis.com/css2?family=Questrial&family=Open+Sans:wght@400;600;700&family=Mulish:wght@700;800&display=swap">
<style>
:root{
  --blue:#1479c4;
  --blue-dark:#0b5ea6;
  --blue-light:#2a93e0;
  --ink:#222;
  --text:#555;
  --muted:#777;
  --line:#e3e3e3;
  --panel:#f3f3f3;
  --footer:#3a3a3a;
  --footer-deep:#2c2c2c;
  --footer-text:#a9a9a9;
}
*{box-sizing:border-box;margin:0;padding:0}
html,body{width:1200px;height:2368px;overflow:hidden;background:#fff}
body{position:relative;font-family:"Open Sans",Arial,sans-serif;color:var(--text);font-size:12px}
a{color:inherit;text-decoration:none}

/* header */
.brand{position:absolute;left:98px;top:32px;font-family:"Mulish",sans-serif;font-weight:800;font-size:30px;color:var(--blue);letter-spacing:.5px;white-space:nowrap}
.contact{position:absolute;top:32px;right:98px;display:flex;gap:18px;align-items:center;font-size:15px;color:#444;white-space:nowrap}
.contact-item{display:flex;align-items:center;gap:12px}
.contact-icon{width:42px;height:42px;border:2px solid var(--blue);border-radius:50%;display:flex;align-items:center;justify-content:center}

/* nav */
.main-nav{position:absolute;left:98px;top:99px;width:1004px;height:54px;display:flex;background:linear-gradient(#2290dc,#0c63ad);border-radius:3px 3px 0 0;z-index:2}
.main-nav a{font-family:"Questrial",sans-serif;color:#fff;font-size:14px;white-space:nowrap;display:flex;align-items:center;justify-content:center;border-right:1px solid rgba(0,0,0,.2);border-left:1px solid rgba(255,255,255,.15)}
.main-nav a.active{background:linear-gradient(#1d7fc7,#0a5494);box-shadow:inset 0 0 6px rgba(0,0,0,.3)}
.main-nav a:last-child{border-right:0}

/* hero */
.hero{position:absolute;left:0;top:153px;width:1200px;height:420px;background:linear-gradient(100deg,#5b6670 0%,#b9b3a6 30%,#8c7a6d 50%,#6d5e4f 70%,#3c3a38 100%)}
.hero-caption{position:absolute;left:98px;top:107px;width:365px;height:218px;background:rgba(60,60,60,.6);padding:22px 18px;color:#fff}
.hero-caption h1{font-family:"Questrial",sans-serif;font-size:32px;font-weight:700;margin-bottom:14px;white-space:nowrap}
.hero-caption p{font-size:12.5px;line-height:21px;margin-bottom:20px}
.btn{display:inline-block;background:linear-gradient(#2593df,#0b5ea6);color:#fff;border-radius:3px;font-size:12.5px;white-space:nowrap}
.hero-caption .btn{padding:12px 18px}
.hero-arrow{position:absolute;top:168px;width:44px;height:44px;background:rgba(0,0,0,.6);display:flex;align-items:center;justify-content:center}
.hero-arrow.prev{left:0}.hero-arrow.next{right:0}

/* section titles */
.section-title{position:absolute;display:flex;align-items:center;gap:12px;font-family:"Mulish",sans-serif;font-weight:700;font-size:19px;color:var(--ink);letter-spacing:.5px;white-space:nowrap}

/* event cards */
.event-card{position:absolute;left:98px;width:688px;height:290px;border:1px solid var(--line);border-top:2px dashed #cfcfcf;box-shadow:0 1px 4px rgba(0,0,0,.08);background:#fff}
.event-card h2{position:absolute;left:19px;top:16px;font-family:"Questrial",sans-serif;font-weight:400;font-size:21px;color:var(--blue);white-space:nowrap}
.event-photo{position:absolute;left:19px;top:64px;width:160px;height:172px}
.event-body{position:absolute;left:189px;top:58px;width:478px;font-size:12px;line-height:20.5px}
.event-body p{text-align:justify;color:#555}
.event-body .more{color:var(--blue);text-decoration:underline}
.meta{margin-top:6px;line-height:23px;white-space:nowrap}
.meta b{color:var(--blue);font-weight:400}
.price{font-weight:700;color:var(--blue);font-size:15.5px;margin-top:9px}
.event-body .btn{margin-top:10px;padding:11px 12px;font-size:14px}

/* sidebar */
.side-box{position:absolute;left:816px;width:285px;background:var(--panel);padding:22px 17px}
.side-box h3{display:flex;align-items:center;gap:10px;font-family:"Mulish",sans-serif;font-size:19px;font-weight:700;color:var(--ink);letter-spacing:.5px;white-space:nowrap}
.subscribe p{font-size:12px;line-height:20px;margin-top:10px;text-align:justify}
.mail-field{margin-top:14px;height:44px;background:#fff;border:1px solid #ccc;border-radius:3px;display:flex;align-items:center;gap:12px;padding:0 13px;font-size:11px;color:#555}
.subscribe .btn{margin-top:14px;padding:7px 9px;font-size:11px}
.news-item{display:flex;gap:12px;margin-top:20px}
.news-thumb{width:73px;height:65px;flex:none}
.news-item a{display:block;color:var(--blue);font-size:12px;line-height:20px}
.news-item span{display:block;font-size:12px;margin-top:6px;color:#555}
.ad{position:absolute;left:816px;top:1342px;width:285px;height:253px;background:radial-gradient(circle at 50% 45%,#5d6a2a 0%,#1d2414 45%,#0b0d0a 100%)}
.ad-tag{position:absolute;left:0;bottom:0;background:var(--blue);color:#fff;font-size:12px;padding:6px 10px}

/* blog */
.blog-card{position:absolute;top:1675px;width:238px;height:343px;background:#fff;box-shadow:0 2px 5px rgba(0,0,0,.15)}
.blog-photo{height:158px}
.blog-text{padding:10px 19px}
.blog-text h4{font-weight:400;font-size:12px;line-height:20px;color:var(--blue)}
.blog-text .date{margin-top:3px;font-size:12px}
.blog-text p{margin-top:11px;font-size:12px;line-height:20.5px;text-align:justify}
.blog-text .more{display:block;margin-top:6px;color:var(--blue);font-size:12px}

/* footer */
.site-footer{position:absolute;left:0;top:2056px;width:1200px;height:252px;background:var(--footer)}
.footer-col{position:absolute;top:26px;width:230px;height:210px}
.footer-col::after{content:"";position:absolute;right:0;top:0;width:1px;height:100%;box-shadow:6px 0 10px rgba(0,0,0,.45)}
.footer-col h5{font-family:"Mulish",sans-serif;font-size:14.5px;color:#fff;letter-spacing:.5px;margin-bottom:10px}
.footer-col a{display:block;color:var(--footer-text);font-size:12px;line-height:20.5px;white-space:nowrap}
.footer-brand{position:absolute;right:98px;top:30px;font-family:"Mulish",sans-serif;font-weight:800;font-size:28px;color:#7a7a7a;text-align:right;white-space:nowrap}
.social{position:absolute;right:98px;top:84px;display:flex;gap:10px}
.social span{width:36px;height:36px;border-radius:50%;background:#484848}
.bottom-bar{position:absolute;left:0;top:2308px;width:1200px;height:60px;background:var(--footer-deep);text-align:center;line-height:60px;font-size:11px;color:#6d6d6d}
</style>
</head>
<body>

<header>
  <div class="brand">KELVARA EVENTS</div>
  <div class="contact">
    <div class="contact-item">
      <span class="contact-icon"><svg width="18" height="18" viewBox="0 0 24 24"><path fill="#1479c4" d="M6.6 10.8a15.1 15.1 0 0 0 6.6 6.6l2.2-2.2a1 1 0 0 1 1-.25 11.4 11.4 0 0 0 3.6.57 1 1 0 0 1 1 1V20a1 1 0 0 1-1 1A17 17 0 0 1 3 4a1 1 0 0 1 1-1h3.5a1 1 0 0 1 1 1c0 1.25.2 2.45.57 3.57a1 1 0 0 1-.25 1z"/></svg></span>
      <span>0800 472 615</span>
    </div>
    <div class="contact-item">
      <span class="contact-icon"><svg width="18" height="14" viewBox="0 0 24 18"><path fill="#1479c4" d="M0 0h24v2L12 9 0 2zM0 4l12 7 12-7v14H0z"/></svg></span>
      <span>info@kelvaraevents.com</span>
    </div>
  </div>
</header>

<nav class="main-nav">
  <a class="active" href="#" style="width:90px">Home</a>
  <a href="#" style="width:155px">Events by Region</a>
  <a href="#" style="width:184px">Events by Town/City</a>
  <a href="#" style="width:160px">Events for Women</a>
  <a href="#" style="width:180px">Workshops/Seminars</a>
  <a href="#" style="width:130px">Business Shows</a>
  <a href="#" style="width:105px">Blog</a>
</nav>

<section class="hero" role="img" aria-label="Photo of colleagues networking around a table with laptops">
  <div class="hero-caption">
    <h1>Networking Events</h1>
    <p>Neque porro quisquam est qui dolorem ipsum quia dolor sit amet, consectetur, adipisci velit...</p>
    <a class="btn" href="#">Read More</a>
  </div>
  <span class="hero-arrow prev"><svg width="12" height="18" viewBox="0 0 12 18"><path d="M10 2 3 9l7 7" stroke="#fff" stroke-width="2" fill="none"/></svg></span>
  <span class="hero-arrow next"><svg width="12" height="18" viewBox="0 0 12 18"><path d="m2 2 7 7-7 7" stroke="#fff" stroke-width="2" fill="none"/></svg></span>
</section>

<h2 class="section-title" style="left:98px;top:600px">
  <svg width="20" height="20" viewBox="0 0 20 20"><rect x="1" y="3" width="18" height="16" rx="2" fill="#1479c4"/><rect x="3" y="8" width="14" height="9" fill="#fff"/><rect x="5" y="0" width="2" height="5" fill="#1479c4"/><rect x="13" y="0" width="2" height="5" fill="#1479c4"/><path fill="#1479c4" d="M5 10h2v2H5zm4 0h2v2H9zm4 0h2v2h-2zm-8 4h2v2H5zm4 0h2v2H9z"/></svg>
  EVENTS DIRECTORY
</h2>

<article class="event-card" style="top:660px">
  <h2>Corrin Women Bright Biz Network Lunch Meeting</h2>
  <div class="event-photo" role="img" aria-label="Photo of two businesswomen shaking hands" style="background:linear-gradient(120deg,#e9e4dc,#b99a7a 55%,#3c3632)"></div>
  <div class="event-body">
    <p>We are very pleased to be adding another date to the diary for Sunderland – bringing together great local businesses to network over a morning cuppa. With no sales pitches or formal introductions, <a class="more" href="#">Read More</a></p>
    <div class="meta"><b>When:</b> 08 January 2016 08:00<br><b>Where:</b> Marlow's Tavern, Ferncliff Road, Oldbury Way, SR9 4QT</div>
    <div class="price">Ticket Price: FREE</div>
    <a class="btn" href="#">Attend this Event</a>
  </div>
</article>

<article class="event-card" style="top:985px">
  <h2>Corrin Women Bright Biz Network Lunch Meeting</h2>
  <div class="event-photo" role="img" aria-label="Photo of a team meeting around a desk" style="background:linear-gradient(120deg,#dfe6ee,#8d98a8 50%,#3d4452)"></div>
  <div class="event-body">
    <p>We are very pleased to be adding another date to the diary for Sunderland – bringing together great local businesses to network over a morning cuppa. With no sales pitches or formal introductions, <a class="more" href="#">Read More</a></p>
    <div class="meta"><b>When:</b> 08 January 2016 08:00<br><b>Where:</b> Marlow's Tavern, Ferncliff Road, Oldbury Way, SR9 4QT</div>
    <div class="price">Ticket Price: FREE</div>
    <a class="btn" href="#">Attend this Event</a>
  </div>
</article>

<article class="event-card" style="top:1309px">
  <h2>Corrin Women Bright Biz Network Lunch Meeting</h2>
  <div class="event-photo" role="img" aria-label="Photo of colleagues talking in a bright office" style="background:linear-gradient(120deg,#cfe0ea,#9aa9b2 50%,#4a4e55)"></div>
  <div class="event-body">
    <p>We are very pleased to be adding another date to the diary for Sunderland – bringing together great local businesses to network over a morning cuppa. With no sales pitches or formal introductions, <a class="more" href="#">Read More</a></p>
    <div class="meta"><b>When:</b> 08 January 2016 08:00<br><b>Where:</b> Marlow's Tavern, Ferncliff Road, Oldbury Way, SR9 4QT</div>
    <div class="price">Ticket Price: FREE</div>
    <a class="btn" href="#">Attend this Event</a>
  </div>
</article>

<aside>
  <div class="side-box subscribe" style="top:616px;height:237px">
    <h3><svg width="20" height="18" viewBox="0 0 20 18"><path fill="#1479c4" d="M0 8 20 0 16 18l-6-5-3 4v-5l9-9-11 7z"/></svg>SUBSCRIBE</h3>
    <p>Subscribe newsletter to receive the latest news and updates direct to your inbox.</p>
    <div class="mail-field"><svg width="16" height="12" viewBox="0 0 24 18"><path fill="#555" d="M0 0h24v2L12 9 0 2zM0 4l12 7 12-7v14H0z"/></svg>Enter Your Mail Id</div>
    <a class="btn" href="#">Subscribe</a>
  </div>

  <div class="side-box news" style="top:873px;height:457px">
    <h3><svg width="18" height="20" viewBox="0 0 18 20"><path fill="#1479c4" d="M9 0a2 2 0 0 1 2 2 6 6 0 0 1 4 6v5l3 3v1H0v-1l3-3V8a6 6 0 0 1 4-6 2 2 0 0 1 2-2zm-2 18h4a2 2 0 0 1-4 0z"/></svg>NETWORKING NEWS</h3>
    <div class="news-item"><div class="news-thumb" role="img" aria-label="Photo of a speaker at a breakfast meeting" style="background:linear-gradient(#c9d6e2,#4b5563)"></div><div><a href="#">Alder Suffolk and Cambridge Alder Sunrise of Lowestoft</a><span>Dec 11,2015</span></div></div>
    <div class="news-item"><div class="news-thumb" role="img" aria-label="Photo of a seated audience" style="background:linear-gradient(#a58f78,#3a2f27)"></div><div><a href="#">Alder Suffolk and Cambridge Alder Sunrise of Lowestoft</a><span>Dec 11,2015</span></div></div>
    <div class="news-item"><div class="news-thumb" role="img" aria-label="Photo of two women talking" style="background:linear-gradient(#e5e1dc,#6d5a4d)"></div><div><a href="#">Alder Suffolk and Cambridge Alder Sunrise of Lowestoft</a><span>Dec 11,2015</span></div></div>
    <div class="news-item"><div class="news-thumb" role="img" aria-label="Photo of a small group meeting at a table" style="background:linear-gradient(#e8e6e2,#7b7068)"></div><div><a href="#">Alder Suffolk and Cambridge Alder Sunrise of Lowestoft</a><span>Dec 11,2015</span></div></div>
  </div>

  <div class="ad" role="img" aria-label="Advertisement for a nature documentary series">
    <span class="ad-tag">Ads</span>
  </div>
</aside>

<h2 class="section-title" style="left:98px;top:1628px">
  <svg width="22" height="18" viewBox="0 0 22 18"><rect x="1" y="1" width="20" height="16" rx="2" fill="none" stroke="#1479c4" stroke-width="2"/><rect x="4" y="4" width="6" height="5" fill="#1479c4"/><path stroke="#1479c4" stroke-width="2" d="M12 5h6M12 8h6M4 12h14"/></svg>
  LATEST BLOG POSTS
</h2>

<section class="blog">
  <article class="blog-card" style="left:98px">
    <div class="blog-photo" role="img" aria-label="Photo of friends at an outdoor barbecue" style="background:linear-gradient(135deg,#6f8a45,#d9b48c 55%,#8a6a52)"></div>
    <div class="blog-text"><h4>Blinding Success for Linkwell Member</h4><div class="date">Dec 11,2015</div><p>Neque porro quisquam est, qui dolorem ipsum quia dolor sit amet, consectetur</p><a class="more" href="#">Read More</a></div>
  </article>
  <article class="blog-card" style="left:353px">
    <div class="blog-photo" role="img" aria-label="Photo of guests holding glasses at an evening reception" style="background:linear-gradient(135deg,#2a1d18,#8a4a3a 50%,#1c1412)"></div>
    <div class="blog-text"><h4>Blinding Success for Linkwell Member</h4><div class="date">Dec 11,2015</div><p>Neque porro quisquam est, qui dolorem ipsum quia dolor sit amet, consectetur</p><a class="more" href="#">Read More</a></div>
  </article>
  <article class="blog-card" style="left:608px">
    <div class="blog-photo" role="img" aria-label="Photo of a conference audience facing a stage" style="background:linear-gradient(180deg,#d8c9c2,#6a5048 55%,#2b2220)"></div>
    <div class="blog-text"><h4>Blinding Success for Linkwell Member</h4><div class="date">Dec 11,2015</div><p>Neque porro quisquam est, qui dolorem ipsum quia dolor sit amet, consectetur</p><a class="more" href="#">Read More</a></div>
  </article>
  <article class="blog-card" style="left:863px">
    <div class="blog-photo" role="img" aria-label="Photo of business people chatting at a standing event" style="background:linear-gradient(135deg,#e6e6e6,#8b8a8c 50%,#2f3136)"></div>
    <div class="blog-text"><h4>Blinding Success for Linkwell Member</h4><div class="date">Dec 11,2015</div><p>Neque porro quisquam est, qui dolorem ipsum quia dolor sit amet, consectetur</p><a class="more" href="#">Read More</a></div>
  </article>
</section>

<footer class="site-footer">
  <div class="footer-col" style="left:98px">
    <h5>QUICK LINKS</h5>
    <a href="#">Home</a><a href="#">Events by Region</a><a href="#">Events by Town/City</a><a href="#">Events for Women</a><a href="#">Workshops/Seminars</a><a href="#">Business Shows</a><a href="#">Blog</a><a href="#">Event Franchises</a>
  </div>
  <div class="footer-col" style="left:373px">
    <h5>HELP</h5>
    <a href="#">Login</a><a href="#">Contact Us</a><a href="#">Subscribe News</a><a href="#">Register to Add Events</a><a href="#">Testimonials</a><a href="#">Online Marketing</a><a href="#">Download Guide</a>
  </div>
  <div class="footer-col" style="left:639px">
    <h5>COMPANY</h5>
    <a href="#">About us</a><a href="#">Tags</a><a href="#">Support</a><a href="#">Contact</a><a href="#">Terms &amp; conditions</a><a href="#">Copyright notification</a><a href="#">Privacy policy</a>
  </div>
  <div class="footer-brand">KELVARA EVENTS</div>
  <div class="social"><span></span><span></span><span></span></div>
</footer>
<div class="bottom-bar">Copyright © 2016 Kelvara Events. All Right Reserved.</div>

</body>
</html>
```